SaaS Early tech startup business card design

Unique design for experience ecommerce platform company. the business cards will be used by executive members. conformance with color code is required.

```html
<!DOCTYPE html>
<html lang="en">
<head>
<meta charset="utf-8">
<title>nuvek – Business Card</title>
<link href="https://fonts.googleapis.com/css2?family=Lato:wght@700;900&family=Arimo:wght@400&display=swap" rel="stylesheet">
<style>
  :root {
    --page-bg: #eceff1;
    --brand-navy: #067496;
    --brand-teal: #03a898;
    --text-light: #ffffff;
    --logo-ink: #0a6f8f;
    --window-light: #f4f2f2;
    --window-edge: #e2dede;
  }
  * { margin: 0; padding: 0; box-sizing: border-box; }
  html, body {
    width: 1200px;
    height: 900px;
    overflow: hidden;
    background: var(--page-bg);
  }
  .business-card {
    position: absolute;
    left: 100px;
    top: 141px;
    width: 1000px;
    height: 618px;
    overflow: hidden;
    box-shadow: 0 12px 32px rgba(0, 0, 0, 0.18);
    font-family: "Arimo", Arial, sans-serif;
    color: var(--text-light);
  }
  .band-top {
    position: absolute;
    left: 0; top: 0;
    width: 100%; height: 309px;
    background: var(--brand-navy);
  }
  .band-bottom {
    position: absolute;
    left: 0; top: 309px;
    width: 100%; height: 309px;
    background: var(--brand-teal);
  }
  .identity {
    position: absolute;
    left: 38px;
    top: 64px;
  }
  .identity .person-name {
    font-family: "Lato", Arial, sans-serif;
    font-weight: 700;
    font-size: 43px;
    letter-spacing: -0.5px;
    line-height: 1;
  }
  .identity .person-role {
    font-size: 30px;
    line-height: 1;
    margin-top: 4px;
  }
  .contact-list {
    position: absolute;
    left: 38px;
    top: 356px;
    list-style: none;
  }
  .contact-list li {
    display: flex;
    align-items: center;
    gap: 10px;
    font-size: 30px;
    height: 36px;
    line-height: 36px;
  }
  .contact-list svg {
    width: 25px;
    height: 25px;
    flex: none;
  }
  .postal-address {
    position: absolute;
    left: 38px;
    top: 484px;
    font-size: 30px;
    line-height: 36px;
    font-style: normal;
  }
  .frosted-window {
    position: absolute;
    left: 435px;
    top: 58px;
    width: 502px;
    height: 502px;
    border-radius: 50%;
    background: radial-gradient(circle at 50% 45%, var(--window-light) 0%, var(--window-light) 55%, var(--window-edge) 100%);
  }
  .brand-wordmark {
    position: absolute;
    left: 435px;
    top: 58px;
    width: 502px;
    height: 502px;
    display: flex;
    align-items: center;
    justify-content: center;
    font-family: "Lato", Arial, sans-serif;
    font-weight: 900;
    font-size: 150px;
    letter-spacing: -2px;
    color: var(--logo-ink);
    line-height: 1;
    padding-bottom: 10px;
  }
</style>
</head>
<body>
  <article class="business-card">
    <div class="band-top"></div>
    <div class="band-bottom"></div>

    <header class="identity">
      <h1 class="person-name">DANIEL REYES</h1>
      <p class="person-role">Managing Director</p>
    </header>

    <ul class="contact-list">
      <li>
        <svg viewBox="0 0 24 24" fill="none" stroke="#ffffff" stroke-width="2" stroke-linecap="round" stroke-linejoin="round" aria-hidden="true">
          <path d="M5 3h4l2 5-2.5 1.5a11 11 0 0 0 6 6L16 13l5 2v4a2 2 0 0 1-2 2A16 16 0 0 1 3 5a2 2 0 0 1 2-2z"/>
          <path d="M15 3a6 6 0 0 1 6 6"/>
          <path d="M15 7a2 2 0 0 1 2 2"/>
        </svg>
        <span>044-987 654 321</span>
      </li>
      <li>
        <svg viewBox="0 0 24 24" aria-hidden="true">
          <rect x="2" y="5" width="20" height="14" fill="#ffffff"/>
          <path d="M2 5l10 8 10-8" fill="none" stroke="#03a898" stroke-width="1.6"/>
        </svg>
        <span>hello@nuvekmail.com</span>
      </li>
      <li>
        <svg viewBox="0 0 24 24" fill="none" stroke="#ffffff" stroke-width="1.6" aria-hidden="true">
          <circle cx="12" cy="12" r="10"/>
          <ellipse cx="12" cy="12" rx="4.5" ry="10"/>
          <path d="M2 12h20M4 7h16M4 17h16"/>
        </svg>
        <span>www.nuvekshop.com</span>
      </li>
    </ul>

    <address class="postal-address">
      88, Harbour Lane Suite 4<br>
      10234,Northland
    </address>

    <div class="frosted-window" role="img" aria-label="Round frosted clear window in the card, showing whatever is behind it"></div>
    <div class="brand-wordmark">nuvek</div>
  </article>
</body>
</html>
```